Fresh, modern, fun business card for pediatric dental practice

Need a business card for fresh, modern, fun pediatric dental practice

Clean look that matches our website's font and colors

We prefer the look of curved corners on business cards

Target Market(s)

parents (mothers) of young children, professionals, mid-high class

Industry/Entity Type

Dental

Contact Information for Business Card

Maplebrook Pediatric Dentistry
482 Quarry Lane
Suite 517
Elmstead, PA 17999
717.555.0193
www.maplebrookkidsdental.example

Mei-Ran Tsai, DMD
Corinne Walbeck, DMD
(we are working on our email address, but we would like that on the card as well)

Font styles to use
Sans Serif

Requirements
Must have
• All info; we would also like to make cards for individual staff members
• colors from our website and color palatte, attatched
• use same font and design as website for branding
Nice to have
• clean, simple card that has a pop of color
• we would like to see a few designs with our tag line "where smiles get brighter"
• we are not sure if we want to have it on there or not
• we would like to see a few designs incorporating the ribbon graphic on our website where the word WELCOME is

```html
<!DOCTYPE html>
<html lang="en">
<head>
<meta charset="utf-8">
<title>Maplebrook Pediatric Dentistry — Business Card</title>
<link rel="stylesheet" href="https://fonts.googleapis.com/css2?family=Source+Sans+3:wght@400;600;700&display=swap">
<style>
  :root {
    --backdrop: #272727;
    --kraft-light: #dcbd94;
    --kraft-mid: #c9a274;
    --kraft-dark: #a57c52;
    --ink: #2a2521;
    --rule: #7a6650;
  }
  html, body {
    margin: 0;
    width: 1200px;
    height: 900px;
    overflow: hidden;
    background: var(--backdrop);
    font-family: "Source Sans 3", "Helvetica Neue", Arial, sans-serif;
    color: var(--ink);
  }
  .stage { position: relative; width: 1200px; height: 900px; }
  .card {
    position: absolute;
    top: 306px;
    width: 439px;
    height: 271px;
    border-radius: 4px;
    background: linear-gradient(160deg, var(--kraft-light) 0%, var(--kraft-mid) 55%, var(--kraft-dark) 100%);
    overflow: hidden;
  }
  .card--front { left: 149px; }
  .card--back { left: 608px; }

  .brand { position: absolute; left: 0; right: 0; text-align: center; color: var(--ink); }
  .brand__dot { display: block; margin: 0 auto; border-radius: 50%; background: var(--ink); }
  .brand__name { display: block; line-height: 1; font-weight: 700; letter-spacing: 0.03em; }
  .brand__sub { display: block; line-height: 1; font-weight: 400; letter-spacing: 0.05em; }

  .card--front .brand { top: 33px; }
  .card--front .brand__dot { width: 26px; height: 26px; margin-bottom: 12px; }
  .card--front .brand__name { font-size: 31px; }
  .card--front .brand__sub { font-size: 17px; margin-top: 4px; }

  .card--back .brand { top: 74px; }
  .card--back .brand__dot { width: 40px; height: 40px; margin-bottom: 20px; }
  .card--back .brand__name { font-size: 46px; }
  .card--back .brand__sub { font-size: 23px; margin-top: 6px; }

  .divider { position: absolute; left: 31px; right: 25px; top: 153px; height: 1px; background: var(--rule); }

  .staff { position: absolute; left: 31px; top: 175px; }
  .staff__name { font-size: 15px; font-weight: 600; line-height: 18px; margin: 0; }
  .staff__email { font-size: 9px; line-height: 12px; margin: 0 0 6px; }

  .contact { position: absolute; right: 25px; top: 164px; text-align: right; }
  .contact__line { margin: 0; font-size: 12px; line-height: 17px; display: flex; justify-content: flex-end; align-items: center; gap: 5px; }
  .contact__line svg { width: 9px; height: 9px; }
  .address { margin: 4px 0 0 0; font-size: 10px; line-height: 14px; font-style: normal; }
</style>
</head>
<body>
<main class="stage">
  <section class="card card--front" aria-label="Business card front">
    <div class="brand">
      <span class="brand__dot"></span>
      <span class="brand__name">maplebrook</span>
      <span class="brand__sub">pediatric dentistry</span>
    </div>
    <div class="divider"></div>
    <div class="staff">
      <p class="staff__name">Mei-Ran Tsai, DMD</p>
      <p class="staff__email">mei-ran@maplebrookkidsdental.example</p>
      <p class="staff__name">Corinne Walbeck, DMD</p>
      <p class="staff__email">corinne@maplebrookkidsdental.example</p>
    </div>
    <div class="contact">
      <p class="contact__line">717.555.0193
        <svg viewBox="0 0 10 10" aria-hidden="true"><rect x="2.5" y="0.5" width="5" height="9" rx="1" fill="none" stroke="currentColor" stroke-width="1"/><line x1="4" y1="8" x2="6" y2="8" stroke="currentColor"/></svg>
      </p>
      <p class="contact__line">www.maplebrookkidsdental.example
        <svg viewBox="0 0 10 10" aria-hidden="true"><circle cx="5" cy="5" r="4.5" fill="currentColor"/><path d="M5 .5v9M.5 5h9" stroke="#c9a274" stroke-width=".8"/></svg>
      </p>
      <address class="address">
        Maplebrook Pediatric Dentistry<br>
        482 Quarry Lane, Suite 517<br>
        Elmstead, PA 17999
      </address>
    </div>
  </section>

  <section class="card card--back" aria-label="Business card back">
    <div class="brand">
      <span class="brand__dot"></span>
      <span class="brand__name">maplebrook</span>
      <span class="brand__sub">pediatric dentistry</span>
    </div>
  </section>
</main>
</body>
</html>
```